QVR business card

Need a business card for a company that provides instructional design and elearning development services. The website is here: http://quorvane.studio/

I'm attaching a current logo, as well as the old business card design. While I like to keep it clean, the old design is too simplistic for my liking. The only idea I want to reuse from the old design is placing industry jargon on the back of the card, just need a better way to present it. But if you have other ideas for the back--feel free to experiment.

Please use the colors complementary to the color we have on the website. Thank you!

```html
<!DOCTYPE html>
<html lang="en">
<head>
<meta charset="utf-8">
<title>QVR business card</title>
<link href="https://fonts.googleapis.com/css2?family=Source+Sans+3:wght@400;600;700&display=swap" rel="stylesheet">
<style>
  :root {
    --backdrop: #000000;
    --card: #2e2f33;
    --teal: #3fc2b0;
    --sand: #d8d39a;
    --text: #f1f1f1;
    --divider: #3a3b40;
  }
  * { box-sizing: border-box; margin: 0; padding: 0; }
  html, body {
    width: 1200px; height: 900px; overflow: hidden;
    background: var(--backdrop);
    font-family: "Source Sans 3", "Myriad Pro", sans-serif;
  }
  .canvas { position: relative; width: 1200px; height: 900px; }
  .card {
    position: absolute; top: 271px;
    width: 457px; height: 281px;
    background: var(--card);
    border-radius: 14px;
  }
  .card--front { left: 137px; }
  .card--back { left: 626px; }

  .brand-name {
    position: absolute;
    font-weight: 700;
    color: var(--teal);
    letter-spacing: 2px;
    line-height: 1;
  }
  .card--front .brand-name { left: 42px; top: 114px; font-size: 64px; }
  .card--back .brand-name { left: 48px; top: 114px; font-size: 64px; }

  .divider {
    position: absolute; left: 194px; top: 84px;
    width: 1px; height: 180px; background: var(--divider);
  }
  .holder-name {
    position: absolute; left: 213px; top: 89px;
    font-size: 15px; font-weight: 600; color: var(--teal);
  }
  .contact-list {
    position: absolute; left: 213px; top: 139px;
    list-style: none;
  }
  .contact-list li {
    display: flex; align-items: center; gap: 6px;
    height: 17px; font-size: 13px; color: var(--text);
  }
  .contact-list svg { width: 9px; height: 9px; flex: none; }

  .help-title {
    position: absolute; left: 242px; top: 54px;
    font-size: 19px; font-weight: 600; color: var(--teal);
  }
  .service-list {
    position: absolute; left: 242px; top: 91px;
    list-style: none;
  }
  .service-list li {
    display: flex; align-items: center; gap: 10px;
    height: 24px; font-size: 13px; font-weight: 600; color: var(--text);
  }
  .service-list li::before {
    content: ""; width: 8px; height: 8px; margin-right: 7px;
    background: var(--teal); flex: none;
  }
</style>
</head>
<body>
<div class="canvas">
  <section class="card card--front">
    <div class="brand-name">QVR</div>
    <div class="divider"></div>
    <h1 class="holder-name">Marta Velinsky</h1>
    <ul class="contact-list">
      <li>
        <svg viewBox="0 0 10 10" aria-hidden="true"><path d="M2 1 L4 1 L4.6 3 L3.4 4 Q4.5 6 6 6.6 L7 5.4 L9 6 L9 8 Q8 9 7 9 Q1 8 1 2 Q1 1 2 1 Z" fill="var(--teal)"/></svg>
        555-014-2290
      </li>
      <li>
        <svg viewBox="0 0 10 10" aria-hidden="true"><rect x="0.5" y="2" width="9" height="6.5" fill="var(--teal)"/><path d="M0.5 2 L5 5.5 L9.5 2" stroke="var(--card)" fill="none"/></svg>
        mvelinsky@quorvane.studio
      </li>
      <li>
        <svg viewBox="0 0 10 10" aria-hidden="true"><circle cx="5" cy="5" r="4.5" fill="var(--teal)"/><path d="M0.5 5 H9.5 M5 0.5 Q2.5 5 5 9.5 M5 0.5 Q7.5 5 5 9.5" stroke="var(--card)" stroke-width="0.8" fill="none"/></svg>
        www.quorvane.studio
      </li>
    </ul>
  </section>

  <section class="card card--back">
    <div class="brand-name">QVR</div>
    <h2 class="help-title">How can we help?</h2>
    <ul class="service-list">
      <li>Mobile Learning Scorm</li>
      <li>Instructional Design Lms</li>
      <li>Moocs Elearning Html5</li>
      <li>Adult Learning Theory</li>
      <li>Gamification Classroom</li>
      <li>Xapi Blended Learning</li>
    </ul>
  </section>
</div>
</body>
</html>
```